Cyber Security Site Design (Products & Consulting)

I need my website redesigned to be engaging, clean, efficient and modern. My company (when its up and running) is going to be concentrated on two things: a few specific products for cyber security as well as cyber security consulting services. The background I bring to the field is having worked with small companies all the way to the largest government organizations and advising them on their security posture and how to improve it. We need the ability to add products and services easily.

For a sample product, you can use either Tarnet (http://www.tarnet-relay.org/) or Verodyne Ashmantle (https://www.verodyne.com/products/relay-hx-and-fortified-edge-portal).

It will replace https://lumerafieldworks.com/

Target Market(s)

Cyber Security professionals in all verticals

Coding

Coded - Design and coding required

Number of Pages Required

4 page

Font styles to use
Sans Serif

Colors
6b449b

Requirements
Must have
• Ability to easily modify
• Have main page
• Have product specific pages
• Have consulting services pages
• Have executive team information
• Clean, modern design
• Usage of the logo and its color scheme
Nice to have
• I like the idea of a left collapsed sidebar (so icons only) that can expand for text.
• I am also open to a very unique landing page, possibly a shape in the middle (hexagons maybe?) with each of the options there.
Should not have
• Nothing that looks like it came out of a hacker movie

```html
<!DOCTYPE html>
<html lang="en">
<head>
<meta charset="utf-8">
<title>Lumera Fieldworks — Our Products</title>
<link href="https://fonts.googleapis.com/css2?family=Titillium+Web:wght@300;400;600;700&family=Roboto:wght@400;500&family=Montserrat:wght@400&display=swap" rel="stylesheet">
<style>
:root{
  --purple:#6b449b;
  --purple-footer:#623796;
  --purple-deep:#532c80;
  --ink:#1e1e24;
  --text:#4a4a55;
  --panel:#f2f2f4;
  --rule:#dcdce2;
  --white:#ffffff;
}
*{margin:0;padding:0;box-sizing:border-box}
html,body{width:842px;height:1200px;overflow:hidden;background:var(--white)}
body{position:relative;font-family:"Roboto",sans-serif;color:var(--ink)}
.abs{position:absolute}

/* header */
.site-header{left:0;top:0;width:842px;height:50px;background:var(--white)}
.brand{left:99px;top:10px;display:flex;align-items:center;gap:6px}
.brand-mark{width:18px;height:18px;background:var(--purple)}
.brand-name{font-family:"Titillium Web",sans-serif;font-weight:600;font-size:19px;color:var(--purple);letter-spacing:.5px;line-height:1}
.nav{left:318px;top:19px;display:flex;gap:24px;font-size:8.6px;letter-spacing:.2px}
.nav a{color:var(--ink);text-decoration:none}
.nav a.current{color:var(--purple)}
.btn{display:flex;align-items:center;gap:6px;background:var(--purple);color:var(--white);border-radius:12px;font-size:8.4px;font-weight:500;letter-spacing:.2px;padding:0 10px;box-shadow:0 2px 5px rgba(60,30,100,.3)}
.btn-dot{width:12px;height:12px;border:2px solid var(--white);border-radius:50%}
.btn-contact{left:650px;top:14px;height:22px}

/* hero */
.hero-photo{left:0;top:50px;width:842px;height:261px;background:linear-gradient(180deg,#6f7f98 0%,#a08f8a 35%,#8a6a57 60%,#5e4a44 100%);clip-path:polygon(0 0,100% 0,100% 68%,50% 100%,0 68%)}
.hero-shade{left:0;top:50px;width:842px;height:261px;background:rgba(20,20,40,.18);clip-path:polygon(0 0,100% 0,100% 68%,50% 100%,0 68%)}
.hero-title{left:0;top:130px;width:842px;text-align:center;font-family:"Titillium Web",sans-serif;font-weight:700;font-size:31px;color:var(--white);letter-spacing:.3px;text-shadow:0 2px 4px rgba(0,0,0,.3)}
.hero-sub{left:0;top:170px;width:842px;text-align:center;font-family:"Titillium Web",sans-serif;font-weight:400;font-size:12.6px;color:var(--white);text-shadow:0 1px 3px rgba(0,0,0,.45)}
.btn-hero{left:359px;top:208px;height:21px;padding:0 10px}

.crumbs{left:99px;top:302px;font-size:9.2px;display:flex;gap:9px;color:var(--ink)}
.crumbs .here{color:var(--purple)}

/* products */
.section-title{left:0;top:358px;width:842px;text-align:center;font-family:"Titillium Web",sans-serif;font-size:28px;font-weight:400;color:var(--ink);letter-spacing:.3px}
.section-title b{font-weight:700}
.title-rule{left:327px;top:405px;width:189px;height:1px;background:var(--rule)}
.title-accent{left:407px;top:404px;width:29px;height:3px;background:var(--purple)}

.product-menu{left:100px;top:429px;width:193px;height:300px;background:var(--panel)}
.menu-item{position:absolute;left:12px;width:170px;height:38px;display:flex;align-items:center;gap:12px;font-family:"Titillium Web",sans-serif;font-size:11.4px;color:var(--ink);border-bottom:1px solid var(--rule)}
.menu-item.last{border-bottom:none}
.menu-item svg{width:22px;height:22px;flex:none}
.menu-active{left:100px;top:467px;width:207px;height:35px;background:var(--purple);clip-path:polygon(0 0,186px 0,100% 50%,186px 100%,0 100%)}
.menu-active-label{left:114px;top:467px;height:35px;display:flex;align-items:center;gap:12px;font-family:"Titillium Web",sans-serif;font-size:11.4px;color:var(--white)}

.detail{left:321px;top:433px;width:420px}
.detail h2{font-family:"Titillium Web",sans-serif;font-weight:400;font-size:14.2px;color:var(--purple);margin-bottom:8px}
.detail p{font-family:"Montserrat",sans-serif;font-size:8.8px;line-height:16px;color:var(--text);text-align:justify;margin-bottom:6px}

/* footer */
.footer-band{left:0;top:783px;width:842px;height:381px;background:var(--purple-footer);clip-path:polygon(0 29px,50% 0,100% 29px,100% 100%,0 100%)}
.footer-rule{left:0;top:861px;width:842px;height:1px;background:rgba(255,255,255,.08)}
.footer-brand{left:0;top:812px;width:842px;display:flex;justify-content:center;align-items:center;gap:7px}
.footer-brand .brand-mark{background:var(--white);width:22px;height:22px}
.footer-brand .brand-name{color:var(--white);font-size:23px}

.cta-title{left:95px;top:890px;font-family:"Titillium Web",sans-serif;font-weight:400;font-size:25px;color:var(--white);letter-spacing:.3px;line-height:30px}
.cta-title b{font-weight:700}
.cta-sub{left:99px;top:928px;width:265px;font-size:9.6px;line-height:12px;color:var(--white)}

.col-title{font-family:"Titillium Web",sans-serif;font-size:11.4px;color:var(--white);font-weight:600}
.col-rule{width:30px;height:1px;background:rgba(255,255,255,.7);margin-top:5px}
.contact-col{left:97px;top:986px;width:180px;color:var(--white)}
.contact-row{display:flex;gap:9px;margin-top:10px;font-size:7.8px;line-height:12px}
.contact-row svg{flex:none;width:8px;height:10px;margin-top:1px}
.contact-row strong{font-weight:500;font-size:8.2px;display:block}
.contact-row .phone{font-size:11px;font-weight:500;letter-spacing:.3px}
.links-col{left:280px;top:986px;color:var(--white)}
.links-col ul{list-style:none;margin-top:11px}
.links-col li{font-size:7.8px;line-height:13.5px;display:flex;gap:8px}
.links-col li::before{content:"›"}

.form-card{left:431px;top:895px;width:312px;height:270px;background:var(--white)}
.field{position:absolute;left:25px;width:262px;height:26px;border:1px solid #c9c9cf;font-family:"Montserrat",sans-serif;font-size:8px;color:#6d6d77;padding:8px 10px}
.field.message{height:41px}
.btn-submit{left:456px;top:1119px;height:23px;padding:0 11px}

.bottom-bar{left:0;top:1164px;width:842px;height:36px;background:var(--purple-deep)}
.copyright{left:99px;top:1176px;font-size:7.8px;color:var(--white)}
.copyright b{font-weight:500}
.social{left:548px;top:1172px;display:flex;gap:5px}
.social span{width:20px;height:20px;border:1px solid rgba(255,255,255,.85);border-radius:50%;display:flex;align-items:center;justify-content:center}
.social span::after{content:"";width:7px;height:7px;background:var(--white)}
</style>
</head>
<body>

<header class="abs site-header">
  <div class="abs brand"><span class="brand-mark"></span><span class="brand-name">LUMERA</span></div>
  <nav class="abs nav">
    <a href="#">HOME</a><a href="#">ABOUT</a><a href="#">OUR TEAM</a><a href="#" class="current">OUR PRODUCTS</a><a href="#">SERVICES</a>
  </nav>
  <a class="abs btn btn-contact"><span class="btn-dot"></span>CONTACT US</a>
</header>

<div class="abs hero-photo" role="img" aria-label="City skyline at dusk with downtown towers"></div>
<div class="abs hero-shade"></div>
<h1 class="abs hero-title">CYBER SECURITY CONSULTING &amp; PRODUCTS</h1>
<p class="abs hero-sub">A full range of Cyber Security Consulting Services and Products to meet your business requirements</p>
<a class="abs btn btn-hero"><span class="btn-dot"></span>GET STARTED NOW!</a>

<div class="abs crumbs"><span>HOME</span><span>»</span><span class="here">OUR PRODUCTS</span></div>

<h2 class="abs section-title">OUR <b>PRODUCTS</b></h2>
<div class="abs title-rule"></div>
<div class="abs title-accent"></div>

<aside class="abs product-menu">
  <div class="menu-item" style="top:0">
    <svg viewBox="0 0 24 24" fill="none" stroke="#333" stroke-width="1.4"><path d="M12 2l8 3v6c0 5-3.5 9-8 11-4.5-2-8-6-8-11V5z"/><path d="M8 12l3 3 5-6"/></svg>Integrated Cyber Defense</div>
  <div class="menu-item" style="top:73px">
    <svg viewBox="0 0 24 24" fill="none" stroke="#333" stroke-width="1.4"><rect x="4" y="6" width="14" height="12" rx="2"/><path d="M8 14v-2M11 14v-4M14 14v-3"/></svg>Information Protection</div>
  <div class="menu-item" style="top:111px">
    <svg viewBox="0 0 24 24" fill="none" stroke="#333" stroke-width="1.4"><path d="M5 2h9l4 4v9M5 2v20h9"/><rect x="13" y="15" width="8" height="6" rx="1"/><path d="M15 15v-2a2 2 0 014 0v2"/></svg>Endpoint Security</div>
  <div class="menu-item" style="top:149px">
    <svg viewBox="0 0 24 24" fill="none" stroke="#333" stroke-width="1.4"><path d="M12 2l8 3v6c0 5-3.5 9-8 11-4.5-2-8-6-8-11V5z"/><rect x="7.5" y="8" width="9" height="6"/><path d="M7.5 8l4.5 3.5L16.5 8"/></svg>Email Security</div>
  <div class="menu-item" style="top:187px">
    <svg viewBox="0 0 24 24" fill="none" stroke="#333" stroke-width="1.4"><circle cx="12" cy="12" r="10"/><path d="M2 12h20M12 2c3 3 3 17 0 20M12 2c-3 3-3 17 0 20"/></svg>Network Security</div>
  <div class="menu-item" style="top:225px">
    <svg viewBox="0 0 24 24" fill="none" stroke="#333" stroke-width="1.4"><path d="M6 17a4 4 0 010-8 6 6 0 0111 1 3.5 3.5 0 011 7"/><rect x="10" y="14" width="7" height="6" rx="1"/><path d="M11.5 14v-2a2 2 0 014 0v2"/></svg>Cloud Security</div>
  <div class="menu-item last" style="top:263px">
    <svg viewBox="0 0 24 24" fill="none" stroke="#333" stroke-width="1.4"><rect x="9" y="2" width="6" height="6"/><rect x="3" y="13" width="7" height="7"/><rect x="13" y="12" width="6" height="6"/></svg>Small Business Products</div>
</aside>
<div class="abs menu-active"></div>
<div class="abs menu-active-label">
  <svg width="22" height="22" viewBox="0 0 24 24" fill="none" stroke="#fff" stroke-width="1.4"><circle cx="11" cy="11" r="8"/><ellipse cx="11" cy="11" rx="5" ry="3"/><circle cx="11" cy="11" r="1.4"/><path d="M17 17l5 5"/></svg>
  Advanced Threat Protection</div>

<article class="abs detail">
  <h2>Advanced Threat Protection</h2>
  <p>Lorem ipsum dolor sit amet, consectetur adipiscing elit, sed do eiusmod tempor incididunt ut labore et dolore magna aliqua.Sed ut perspiciatis unde omnis iste natus error sit voluptatem accusantium doloremque laudantium, totam rem aperiam, eaque ipsa quae ab illo inventore veritatis et quasi architecto beatae vitae dicta sunt explicabo. Nemo enim ipsam voluptatem quia voluptas sit aspernatur aut odit aut fugit, sed quia consequuntur magni dolores eos qui ratione voluptatem sequi nesciunt.</p>
  <p>Sed ut perspiciatis unde omnis iste natus error sit voluptatem accusantium doloremque laudantium, totam rem aperiam, eaque ipsa quae ab illo inventore veritatis et quasi architecto beatae vitae dicta sunt explicabo. Nemo enim ipsam voluptatem quia voluptas sit aspernatur aut odit aut fugit, sed quia consequuntur magni dolores eos qui ratione voluptatem sequi nesciunt. Neque porro quisquam est, qui dolorem ipsum quia dolor sit amet, consectetur, adipisci velit, sed quia non numquam eius modi tempora incidunt ut labore et dolore magnam aliquam quaerat voluptatem.</p>
</article>

<footer>
  <div class="abs footer-band"></div>
  <div class="abs footer-rule"></div>
  <div class="abs footer-brand"><span class="brand-mark"></span><span class="brand-name">LUMERA</span></div>

  <h3 class="abs cta-title"><b>LET’S</b> GET STARTED</h3>
  <p class="abs cta-sub">Take the first step to growing your business with a FREE consultation and quote.</p>

  <div class="abs contact-col">
    <div class="col-title">Contact Details</div><div class="col-rule"></div>
    <div class="contact-row">
      <svg viewBox="0 0 8 10"><path d="M4 0a3.5 3.5 0 013.5 3.5C7.5 6 4 10 4 10S.5 6 .5 3.5A3.5 3.5 0 014 0z" fill="#fff"/><circle cx="4" cy="3.5" r="1.2" fill="#623796"/></svg>
      <div><strong>LUMERA CYBER SECURITY</strong>840 Cedar Ridge Dr, Suite<br>#210 Austin, TX 78701</div>
    </div>
    <div class="contact-row">
      <svg viewBox="0 0 10 10"><path d="M2 0l2 2.5-1 1.2c.7 1.4 1.8 2.5 3.3 3.3l1.2-1L10 8 8.5 10C4 10 0 6 0 1.5z" fill="#fff"/></svg>
      <span class="phone">555-014-2290</span>
    </div>
    <div class="contact-row">
      <svg viewBox="0 0 10 8"><rect width="10" height="8" fill="#fff"/><path d="M0 0l5 4 5-4" stroke="#623796" fill="none"/></svg>
      <span>info@lumeracybersecurity.com</span>
    </div>
  </div>

  <div class="abs links-col">
    <div class="col-title">Quick Links</div><div class="col-rule"></div>
    <ul><li>Home</li><li>About Us</li><li>Our Team</li><li>Our Products</li><li>Services</li><li>Conatact</li></ul>
  </div>

  <form class="abs form-card">
    <div class="field" style="top:27px">First Name</div>
    <div class="field" style="top:62px">Last Name</div>
    <div class="field" style="top:96px">Email</div>
    <div class="field" style="top:131px">Phone Number</div>
    <div class="field message" style="top:165px">Message</div>
  </form>
  <a class="abs btn btn-submit"><span class="btn-dot"></span>SUBMIT</a>

  <div class="abs bottom-bar"></div>
  <p class="abs copyright">Copyright © 2018 <b>LumeraCyberSecurity</b>. All Right Reserved.</p>
  <div class="abs social" aria-label="Social links"><span></span><span></span><span></span><span></span></div>
</footer>

</body>
</html>
```